A Modern & Sleek "Coming Soon" Page for an A.I Recruiting App

For the “Coming Soon” website, a simple background with no people in it. I've attached an A.I image of what the page should generally look like.

- A single mobile phone as the main focus where the user actually clicks on the, “notify me” button (after entering their email address).
- In the background where the pillars/columns are seen in the example, should be subtle pad locks that are in their opened position with a key inside the lock. I've attached images to try to illustrate this idea, but they are far away in style from what I'm looking for.

SLOGAN: Unlocking the power of meaningful connections
LOGO/TITLE: Should be the name as shown in image with only the name "KelvoLink" on it
COLORS: Purplish/blue hues. Should not be too feminine
NOTE: The user should only click once when signing up/entering their email.

Product: A recruiting platform that matches employers/employees with A.I. and prioritizing cultural fit/values system before skills. The industry we are tackling first is the caregiving industry (nannies, tutors, elderly). All users will be background screened and that info lives on the blockchain. All users will have the option to review and be reviewed/rated.

```html
<!DOCTYPE html>
<html lang="en">
<head>
<meta charset="UTF-8">
<title>KelvoLink — Coming Soon</title>
<link rel="stylesheet" href="https://fonts.googleapis.com/css2?family=Poppins:wght@300;400;600;700&display=swap">
<style>
  :root {
    --bg-deep: #430db4;
    --bg-light: #5418c4;
    --ink: #ffffff;
    --screen-top: #5a2a78;
    --screen-bottom: #2a0f3e;
    --frame: #b9bcc4;
    --frame-dark: #3a3a40;
    --field-line: rgba(255, 255, 255, 0.55);
    --screen-ink: #e9dcf2;
    --lock-main: #6a2fe0;
    --lock-shade: #3c0fa6;
  }
  * { margin: 0; padding: 0; box-sizing: border-box; }
  html, body { width: 1200px; height: 600px; overflow: hidden; }
  body {
    font-family: "Poppins", sans-serif;
    background: linear-gradient(135deg, var(--bg-deep) 0%, var(--bg-light) 100%);
    color: var(--ink);
    position: relative;
  }
  .brand-title {
    position: absolute;
    left: 442px;
    top: 52px;
    font-size: 42px;
    font-weight: 300;
    letter-spacing: 10px;
  }
  .slogan {
    position: absolute;
    left: 446px;
    top: 244px;
    font-size: 26px;
    font-weight: 700;
    line-height: 42px;
  }
  .padlock-art {
    position: absolute;
    left: 728px;
    top: 96px;
    width: 306px;
    height: 392px;
    opacity: 0.75;
  }
  .padlock-shadow {
    position: absolute;
    left: 800px;
    top: 520px;
    width: 240px;
    height: 40px;
    border-radius: 50%;
    background: radial-gradient(ellipse, rgba(40, 0, 110, 0.5), transparent 70%);
  }
  .phone {
    position: absolute;
    left: 138px;
    top: 72px;
    width: 204px;
    height: 462px;
    border-radius: 34px;
    background: var(--frame-dark);
    border: 4px solid var(--frame);
    padding: 8px;
    transform: rotate(-7deg);
    box-shadow: 10px 14px 30px rgba(20, 0, 60, 0.45);
  }
  .phone-screen {
    width: 100%;
    height: 100%;
    border-radius: 26px;
    background: linear-gradient(180deg, var(--screen-top), var(--screen-bottom));
    position: relative;
    padding: 60px 14px 0;
    text-align: center;
    color: var(--screen-ink);
  }
  .phone-notch {
    position: absolute;
    top: 10px;
    left: 50%;
    width: 56px;
    height: 16px;
    margin-left: -28px;
    background: #000;
    border-radius: 10px;
  }
  .app-name { font-size: 24px; font-weight: 300; letter-spacing: 1px; }
  .app-tagline { font-size: 6px; letter-spacing: 2px; opacity: 0.6; margin-top: 4px; }
  .app-slogan { font-size: 13px; margin-top: 110px; line-height: 16px; }
  .email-field {
    margin-top: 46px;
    height: 36px;
    border: 1.5px solid var(--field-line);
    border-radius: 18px;
    font-size: 13px;
    line-height: 33px;
    text-align: left;
    padding-left: 16px;
    color: #fff;
  }
  .notify-button {
    margin-top: 12px;
    height: 38px;
    border: 1.5px solid var(--field-line);
    border-radius: 19px;
    font-size: 16px;
    font-weight: 700;
    line-height: 35px;
    color: #fff;
  }
  .app-footnote { font-size: 9px; margin-top: 6px; opacity: 0.7; line-height: 12px; }
</style>
</head>
<body>
  <div class="padlock-shadow"></div>
  <svg class="padlock-art" role="img" aria-label="Open padlock with a key in its keyhole, glowing violet" viewBox="0 0 306 392">
    <defs>
      <linearGradient id="lockFill" x1="0" y1="0" x2="1" y2="1">
        <stop offset="0" stop-color="var(--lock-main)"/>
        <stop offset="1" stop-color="var(--lock-shade)"/>
      </linearGradient>
    </defs>
    <rect x="0" y="0" width="306" height="392" rx="40" fill="url(#lockFill)" opacity="0.35"/>
  </svg>

  <h1 class="brand-title">KelvoLink</h1>
  <p class="slogan">Unlocking The Power Of<br>Meaningful Connections</p>

  <div class="phone">
    <div class="phone-screen">
      <div class="phone-notch"></div>
      <div class="app-name">KelvoLink</div>
      <div class="app-tagline">CARE · VALUES · TRUST</div>
      <div class="app-slogan">Unlocking power of<br>meaningful connections</div>
      <div class="email-field">Enter Email</div>
      <div class="notify-button">Notify Me</div>
      <div class="app-footnote">Early access for<br>caring minds</div>
    </div>
  </div>
</body>
</html>
```